Personal Injury Lawyer Billboard

I would like a design created featuring the image of the lawyer centered in the middle of the design.
To the left of the lawyer's image it should read "INJURED?"
To the right of the lawyer's image, it should read "CALL DEAN!"
Under Call Dean, include the phone number 318-555-0187.
At the bottom of the design include the lawyers information "Dean Marlowe Accident & Injury Lawyers"
PLEASE REMOVED THE BACKGROUND IMAGERY OF THE PHOTO SUBMITTED. Also, the colors for this design should match the colors shown in the logo (navy, white and relective soft gold). Please use those color combinations in ways that best stand out.

```html
<!DOCTYPE html>
<html lang="en">
<head>
<meta charset="utf-8">
<title>Dean Marlowe Accident &amp; Injury Lawyers – Billboard</title>
<link rel="stylesheet" href="https://fonts.googleapis.com/css2?family=Cinzel:wght@400;500&family=Oswald:wght@500&display=swap">
<style>
  :root {
    --navy: #0c1c4a;
    --navy-deep: #0a1638;
    --gold: #c39a3b;
    --white: #ffffff;
    --backdrop: #e9ebf0;
  }
  * { margin: 0; padding: 0; box-sizing: border-box; }
  html, body {
    width: 1200px;
    height: 879px;
    overflow: hidden;
    background: var(--backdrop);
  }
  .billboard {
    position: absolute;
    left: 0;
    top: 205px;
    width: 1200px;
    height: 469px;
    background: var(--navy);
    overflow: hidden;
  }
  .headline {
    position: absolute;
    left: 28px;
    top: 168px;
    font-family: "Cinzel", serif;
    font-weight: 500;
    font-size: 80px;
    letter-spacing: 2px;
    color: var(--gold);
    line-height: 1;
  }
  .call-to-action {
    position: absolute;
    left: 824px;
    top: 176px;
    font-family: "Cinzel", serif;
    font-weight: 500;
    font-size: 56px;
    letter-spacing: 1px;
    color: var(--gold);
    line-height: 1;
  }
  .phone {
    position: absolute;
    left: 824px;
    top: 243px;
    display: flex;
    align-items: center;
    gap: 14px;
    font-family: "Cinzel", serif;
    font-weight: 400;
    font-size: 44px;
    color: var(--gold);
    line-height: 1;
  }
  .phone-icon { width: 46px; height: 46px; flex: none; }
  .gold-band {
    position: absolute;
    top: 390px;
    height: 62px;
    background: var(--gold);
  }
  .gold-band--left { left: 0; width: 440px; }
  .gold-band--right { left: 825px; width: 375px; }
  .lawyer-portrait {
    position: absolute;
    left: 470px;
    top: 20px;
    width: 320px;
    height: 330px;
    border-radius: 150px 150px 0 0;
    background: linear-gradient(180deg, #6b5a4e 0%, #4a4a5c 35%, #1b2a5a 70%, #16244f 100%);
  }
  .firm-name {
    position: absolute;
    left: 456px;
    top: 350px;
    width: 330px;
    height: 112px;
    background: var(--navy-deep);
    display: flex;
    flex-direction: column;
    align-items: center;
    justify-content: center;
    gap: 4px;
    font-family: "Oswald", sans-serif;
    font-weight: 500;
    color: var(--white);
    text-transform: uppercase;
    line-height: 1;
  }
  .firm-name__principal { font-size: 44px; letter-spacing: 0.5px; }
  .firm-name__rule { width: 300px; height: 2px; background: var(--white); }
  .firm-name__practice { font-size: 21px; letter-spacing: 0.5px; }
</style>
</head>
<body>
  <main class="billboard">
    <h1 class="headline">INJURED</h1>

    <div class="lawyer-portrait" role="img" aria-label="Cut-out portrait of the smiling lawyer in a navy suit and green tie, fist raised"></div>

    <p class="call-to-action">CALL DEAN</p>
    <p class="phone">
      <svg class="phone-icon" viewBox="0 0 46 46" aria-hidden="true">
        <circle cx="23" cy="23" r="20.5" fill="none" stroke="var(--gold)" stroke-width="3"/>
        <path d="M15.5 13.5c1-1 2.3-.9 3 .1l2.2 3.2c.6.9.4 2-.3 2.7l-1.3 1.2c1 2.3 2.9 4.3 5.3 5.4l1.2-1.3c.7-.8 1.9-.9 2.7-.3l3.2 2.2c1 .7 1.1 2 .2 3l-1.6 1.7c-1 1-2.6 1.4-4 .9-5.6-2-10.1-6.5-12-12.1-.5-1.4-.1-3 .9-4z" fill="var(--gold)"/>
        <path d="M25 13.5a8 8 0 0 1 7.5 7.5M25 17.5a4 4 0 0 1 3.5 3.5" fill="none" stroke="var(--gold)" stroke-width="2" stroke-linecap="round"/>
      </svg>
      318-555-0187
    </p>

    <div class="gold-band gold-band--left"></div>
    <div class="gold-band gold-band--right"></div>

    <div class="firm-name">
      <span class="firm-name__principal">Dean Marlowe</span>
      <span class="firm-name__rule"></span>
      <span class="firm-name__practice">Accident &amp; Injury Lawyers</span>
    </div>
  </main>
</body>
</html>
```